SaaS Early tech startup business card design

Unique design for experience ecommerce platform company. the business cards will be used by executive members. conformance with color code is required.

```html
<!DOCTYPE html>
<html lang="en">
<head>
<meta charset="utf-8">
<title>Nuvra Business Card</title>
<link href="https://fonts.googleapis.com/css2?family=Open+Sans:wght@400;700&display=swap" rel="stylesheet">
<style>
  :root {
    --backdrop: #1f1f1f;
    --brand-blue: #17658f;
    --brand-teal: #1fb89a;
    --card-white: #ffffff;
    --ink: #1c1c1c;
  }
  * { margin: 0; padding: 0; box-sizing: border-box; }
  html, body {
    width: 1200px; height: 988px; overflow: hidden;
    background: var(--backdrop);
    font-family: "Open Sans", Arial, sans-serif;
  }
  .stage { position: relative; width: 1200px; height: 988px; }
  .card {
    position: absolute; width: 540px; height: 310px;
    border-radius: 18px; overflow: hidden;
  }
  .card-front {
    left: 70px; top: 110px;
    background: var(--brand-blue);
    display: flex; align-items: center; justify-content: center;
  }
  .card-front .wordmark {
    font-size: 110px; font-weight: 700; color: var(--brand-teal);
    letter-spacing: -2px; line-height: 1;
  }
  .card-back {
    left: 590px; top: 560px;
    background: var(--card-white);
  }
  .card-back .wave { position: absolute; left: 0; bottom: 0; width: 540px; height: 310px; }
  .card-back .accent-tab {
    position: absolute; left: 0; top: 44px; width: 8px; height: 40px;
    background: var(--brand-blue); border-radius: 0 4px 4px 0;
  }
  .card-back .identity { position: absolute; left: 28px; top: 38px; }
  .card-back .person-name {
    font-size: 30px; font-weight: 700; color: var(--brand-blue); line-height: 1.05;
  }
  .card-back .person-role { font-size: 13px; color: var(--ink); }
  .card-back .wordmark {
    position: absolute; right: 34px; top: 34px;
    font-size: 60px; font-weight: 700; color: var(--brand-teal); line-height: 1;
    letter-spacing: -1px;
  }
  .card-back .address {
    position: absolute; left: 70px; top: 130px;
    font-size: 14px; color: var(--ink); line-height: 1.35;
  }
  .card-back .contact-list {
    position: absolute; left: 70px; top: 196px; list-style: none;
    font-size: 14px; color: var(--ink); line-height: 1.55;
  }
  .card-back .contact-list li { display: flex; align-items: center; gap: 8px; }
  .card-back .contact-list svg { width: 11px; height: 11px; fill: var(--brand-blue); }
</style>
</head>
<body>
<main class="stage">
  <section class="card card-front">
    <span class="wordmark">nuvra</span>
  </section>

  <section class="card card-back">
    <svg class="wave" viewBox="0 0 540 310" aria-hidden="true">
      <path d="M0 300 L330 230 C370 222 380 175 430 165 L540 140 L540 310 L0 310 Z" fill="var(--brand-blue)"/>
      <path d="M0 290 L330 226 C345 222 352 214 360 208 C345 222 335 226 320 230 L0 296 Z" fill="var(--brand-teal)"/>
    </svg>
    <div class="accent-tab"></div>
    <div class="identity">
      <div class="person-name">Dana Reyes</div>
      <div class="person-role">Managing Director</div>
    </div>
    <span class="wordmark">nuvra</span>
    <p class="address">Your location street here,<br>Country name, Country - 91542</p>
    <ul class="contact-list">
      <li><svg viewBox="0 0 12 12"><path d="M2 1h3l1 3-2 1a7 7 0 0 0 3 3l1-2 3 1v3a1 1 0 0 1-1 1A10 10 0 0 1 1 2a1 1 0 0 1 1-1z"/></svg>+000 555 0142</li>
      <li><svg viewBox="0 0 12 12"><path d="M0 2h12v8H0z M0 2l6 5 6-5" /></svg>hello@nuvra.io</li>
      <li><svg viewBox="0 0 12 12"><circle cx="6" cy="6" r="6"/></svg>www.nuvra.io</li>
    </ul>
  </section>
</main>
</body>
</html>
```